Mental Health care Company in Washington DC

We are a new mental health care services provider in Washington DC. Please look at these sites.
https://brightwaterfamilysupport.com
https://www.quietharborinc.com
https://willowgate-dc.org/
https://www.tidepathdc.com
https://www.thelanternofdc.com

```html
<!DOCTYPE html>
<html lang="en">
<head>
<meta charset="utf-8">
<title>Novo Health Services — Mental Health Care in Washington, DC</title>
<link href="https://fonts.googleapis.com/css2?family=Poppins:wght@400;500;600;700&display=swap" rel="stylesheet">
<style>
:root{
  --navy:#0f2a47;
  --navy-deep:#0b2139;
  --orange:#f47b20;
  --teal:#5ab3c3;
  --teal-soft:#cdeaf0;
  --ice:#eef7f9;
  --text:#4a5566;
  --muted:#7c8696;
  --white:#ffffff;
  --line:#e3e9ee;
}
*{box-sizing:border-box;margin:0;padding:0}
html,body{width:1200px;height:3800px;overflow:hidden}
body{font-family:"Poppins",sans-serif;color:var(--text);background:var(--white);position:relative}
.mark{background:var(--teal-soft);padding:0 8px;color:var(--teal)}
.btn{display:inline-block;background:var(--orange);color:var(--white);font-weight:600;font-size:14px;letter-spacing:.5px;padding:15px 28px;border-radius:30px;text-decoration:none}
.photo{border-radius:4px}

/* Header */
.site-header{position:absolute;top:0;left:0;width:1200px;height:92px;background:var(--white);display:flex;align-items:center;padding:0 60px;z-index:3}
.brand{display:flex;align-items:center;gap:10px;font-weight:600;font-size:26px;color:var(--navy)}
.brand-dot{width:14px;height:14px;border-radius:50%;background:var(--orange)}
.main-nav{margin-left:auto;display:flex;gap:30px;font-size:14px;font-weight:500;color:var(--navy)}
.main-nav .active{color:var(--orange)}
.call{display:flex;align-items:center;gap:10px;margin-left:40px}
.call-icon{width:40px;height:40px;border-radius:50%;background:var(--orange);display:flex;align-items:center;justify-content:center}
.call small{display:block;font-size:11px;color:var(--muted);font-weight:600}
.call strong{font-size:16px;color:var(--navy)}

/* Hero */
.hero{position:absolute;top:92px;left:0;width:1200px;height:740px}
.hero-photo{position:absolute;inset:0;background:linear-gradient(100deg,#f4f2ee 0%,#e7e2da 35%,#c9bfb2 60%,#8f8a85 100%)}
.hero-fade{position:absolute;inset:0;background:linear-gradient(90deg,rgba(255,255,255,.9) 0%,rgba(255,255,255,.6) 38%,rgba(255,255,255,0) 60%)}
.hero-copy{position:absolute;left:90px;top:200px;width:520px}
.hero h1{font-size:62px;line-height:1.12;color:var(--navy);font-weight:700}
.hero p{margin-top:18px;font-size:17px;line-height:1.6;color:var(--navy)}
.hero-actions{margin-top:36px;display:flex;align-items:center;gap:30px}
.link-light{color:var(--navy);font-weight:600;font-size:14px;letter-spacing:.5px}

/* Feature cards */
.features{position:absolute;top:740px;left:200px;width:800px;display:flex;gap:24px;z-index:2}
.feature{flex:1;height:230px;background:var(--white);box-shadow:0 12px 30px rgba(15,42,71,.1);display:flex;flex-direction:column;align-items:center;justify-content:center;gap:24px}
.feature-icon{width:92px;height:92px;border-radius:50%;background:var(--teal);display:flex;align-items:center;justify-content:center}
.feature.is-highlight .feature-icon{background:var(--orange)}
.feature h3{font-size:17px;color:var(--navy);font-weight:600;text-align:center;line-height:1.3}

/* Welcome */
.welcome{position:absolute;top:1040px;left:0;width:1200px;height:560px;background:var(--white)}
.welcome-photo{position:absolute;left:90px;top:50px;width:520px;height:420px;background:linear-gradient(135deg,#d7dde2,#b8c4cc 50%,#8d9aa4)}
.welcome-copy{position:absolute;left:670px;top:110px;width:440px}
.section-title{font-size:40px;line-height:1.2;color:var(--navy);font-weight:700}
.welcome-copy p{margin-top:22px;font-size:15px;line-height:1.75}

/* Why */
.why{position:absolute;top:1640px;left:0;width:1200px;height:640px;background:linear-gradient(180deg,var(--white),var(--ice))}
.why-copy{position:absolute;left:130px;top:130px;width:500px}
.why-copy > p{margin-top:18px;font-size:15px;line-height:1.7}
.why-list{margin-top:30px;display:grid;grid-template-columns:1fr 1fr;gap:26px 30px}
.why-item{display:flex;gap:12px;font-size:14px;line-height:1.5;color:var(--text)}
.tick{flex:none;width:34px;height:34px;border-radius:50%;border:2px solid var(--teal);display:flex;align-items:center;justify-content:center}
.why-copy .btn{margin-top:36px}
.why-photo{position:absolute;left:640px;top:100px;width:420px;height:440px;background:linear-gradient(150deg,#e6e0d6,#c8bba8 50%,#7a6c5d)}

/* Services */
.services{position:absolute;top:2280px;left:0;width:1200px;height:620px;background:linear-gradient(180deg,var(--ice),var(--white))}
.services-head{text-align:center;margin-top:36px}
.services-head p{margin-top:10px;font-size:15px;color:var(--muted)}
.service-grid{position:absolute;top:180px;left:130px;width:940px;display:flex;gap:22px}
.service{flex:1;background:var(--white);box-shadow:0 8px 24px rgba(15,42,71,.08);padding:14px 14px 26px}
.service-photo{height:160px}
.service h4{margin-top:18px;font-size:16px;color:var(--navy);font-weight:600}
.service p{margin-top:6px;font-size:13px;line-height:1.55}
.service.is-highlight{background:var(--orange)}
.service.is-highlight h4,.service.is-highlight p{color:var(--white)}
.explore{position:absolute;top:540px;width:1200px;text-align:center;font-size:13px;font-weight:600;color:var(--orange);letter-spacing:.5px;text-decoration:underline}

/* Testimonials */
.testimonials{position:absolute;top:2900px;left:0;width:1200px;height:420px;text-align:center}
.quote-mark{position:absolute;left:130px;top:40px;font-size:220px;line-height:1;color:#f2ece6;font-weight:700}
.testimonials .section-title{position:relative;margin-top:60px}
.testimonials blockquote{position:relative;width:700px;margin:28px auto 0;font-size:15px;line-height:1.8}
.client-name{margin-top:20px;font-weight:600;color:var(--orange);font-size:16px}
.client-role{font-size:12px;color:var(--muted)}
.arrow{position:absolute;top:210px;width:34px;height:34px;border-radius:50%;background:var(--white);box-shadow:0 4px 12px rgba(15,42,71,.15);display:flex;align-items:center;justify-content:center}

/* CTA */
.cta{position:absolute;top:3300px;left:110px;width:980px;height:120px;border-radius:60px;background:var(--orange);display:flex;align-items:center;padding:0 40px 0 70px;z-index:2}
.cta h2{color:var(--white);font-size:34px;font-weight:700}
.cta-btn{margin-left:auto;background:var(--white);color:var(--navy);font-size:13px;font-weight:600;padding:15px 26px;border-radius:30px;letter-spacing:.5px}
.cta-phone{margin-left:14px;width:48px;height:48px;border-radius:50%;background:var(--white);display:flex;align-items:center;justify-content:center}

/* Footer */
.site-footer{position:absolute;top:3360px;left:0;width:1200px;height:440px;background:var(--navy);color:#c5d0dc}
.footer-brand{position:absolute;left:130px;top:150px;display:flex;align-items:center;gap:10px;font-size:26px;font-weight:600;color:var(--white)}
.footer-col{position:absolute;top:120px}
.footer-col h5{font-size:15px;color:var(--white);font-weight:600;margin-bottom:16px}
.footer-col li{list-style:none;font-size:13px;line-height:2.1;display:flex;align-items:center;gap:8px}
.footer-col li::before{content:"";width:5px;height:5px;border-radius:50%;background:var(--orange)}
.contact-item{display:flex;gap:10px;font-size:13px;line-height:1.5;margin-bottom:14px}
.contact-item svg{flex:none;margin-top:2px}
.contact-item b{display:block;color:var(--white);font-weight:500}
.newsletter p{font-size:13px;line-height:1.5;margin-bottom:16px}
.subscribe{display:flex;align-items:center;width:230px;height:42px;border-radius:21px;background:var(--white);padding:0 4px 0 16px;font-size:12px;color:var(--muted)}
.subscribe span{flex:1}
.subscribe i{width:34px;height:34px;border-radius:50%;background:var(--orange);display:flex;align-items:center;justify-content:center}
.copyright{position:absolute;bottom:0;left:0;width:1200px;height:56px;border-top:1px solid rgba(255,255,255,.12);display:flex;align-items:center;justify-content:center;font-size:13px;color:#aebccb}
</style>
</head>
<body>

<header class="site-header">
  <div class="brand"><span class="brand-dot"></span>Novo Health Services</div>
  <nav class="main-nav">
    <span class="active">HOME</span><span>About Us</span><span>Services</span><span>Resources</span><span>Careers</span><span>Contact Us</span>
  </nav>
  <div class="call">
    <span class="call-icon"><svg width="18" height="18" viewBox="0 0 24 24" fill="#fff"><path d="M6.6 10.8a15.1 15.1 0 0 0 6.6 6.6l2.2-2.2c.3-.3.7-.4 1-.2 1.1.4 2.3.6 3.6.6.6 0 1 .4 1 1V20c0 .6-.4 1-1 1A17 17 0 0 1 3 4c0-.6.4-1 1-1h3.5c.6 0 1 .4 1 1 0 1.3.2 2.5.6 3.6.1.3 0 .7-.2 1z"/></svg></span>
    <div><small>CALL</small><strong>(202) 555-0148</strong></div>
  </div>
</header>

<section class="hero">
  <div class="hero-photo" role="img" aria-label="Counsellor comforting a young woman during a session"></div>
  <div class="hero-fade"></div>
  <div class="hero-copy">
    <h1>Your Partner in Mental <span class="mark">Wellness</span></h1>
    <p>Compassionate, personalized mental health care for individuals, families, and our community.</p>
    <div class="hero-actions">
      <span class="btn">SCHEDULE AN APPOINTMENT</span>
      <span class="link-light">LEARN MORE</span>
    </div>
  </div>
</section>

<div class="features">
  <div class="feature">
    <span class="feature-icon"><svg width="44" height="44" viewBox="0 0 24 24" fill="none" stroke="#fff" stroke-width="1.6"><circle cx="12" cy="8" r="3.5"/><path d="M5 20c0-3.9 3.1-6 7-6s7 2.1 7 6"/></svg></span>
    <h3>Highly Trained<br>Professionals</h3>
  </div>
  <div class="feature is-highlight">
    <span class="feature-icon"><svg width="44" height="44" viewBox="0 0 24 24" fill="none" stroke="#fff" stroke-width="1.6"><path d="M12 20s-7-4.4-7-10a4 4 0 0 1 7-2.6A4 4 0 0 1 19 10c0 5.6-7 10-7 10z"/><path d="M9 11h6M12 8v6"/></svg></span>
    <h3>Quality Behavioral<br>Healthcare</h3>
  </div>
  <div class="feature">
    <span class="feature-icon"><svg width="44" height="44" viewBox="0 0 24 24" fill="none" stroke="#fff" stroke-width="1.6"><circle cx="8" cy="9" r="2.5"/><circle cx="16" cy="9" r="2.5"/><path d="M3 19c0-2.8 2.2-4.5 5-4.5s5 1.7 5 4.5M11 19c0-2.8 2.2-4.5 5-4.5s5 1.7 5 4.5"/></svg></span>
    <h3>Multi-Disciplinary<br>Teams</h3>
  </div>
</div>

<section class="welcome">
  <div class="welcome-photo photo" role="img" aria-label="Therapist taking notes while talking with a client"></div>
  <div class="welcome-copy">
    <h2 class="section-title">Welcome to<br><span class="mark">Novo Health Services</span></h2>
    <p>At Novo Health Services, we believe everyone deserves access to quality mental health care. Based in Washington, DC, our mission is to provide compassionate, culturally sensitive, and personalized services that empower you to live a healthier, more balanced life.</p>
    <p>We are committed to helping you navigate life's challenges through evidence-based care, community support, and a team that truly listens.</p>
  </div>
</section>

<section class="why">
  <div class="why-copy">
    <h2 class="section-title">Why <span class="mark">Choose Us</span></h2>
    <p>We provide expert, compassionate care that's flexible, inclusive, and rooted in the DC community — because your well-being comes first.</p>
    <div class="why-list">
      <div class="why-item"><span class="tick"><svg width="16" height="16" viewBox="0 0 24 24" fill="none" stroke="#5ab3c3" stroke-width="3"><path d="M5 12l5 5 9-10"/></svg></span>Experienced and compassionate team</div>
      <div class="why-item"><span class="tick"><svg width="16" height="16" viewBox="0 0 24 24" fill="none" stroke="#5ab3c3" stroke-width="3"><path d="M5 12l5 5 9-10"/></svg></span>Culturally sensitive, inclusive care</div>
      <div class="why-item"><span class="tick"><svg width="16" height="16" viewBox="0 0 24 24" fill="none" stroke="#5ab3c3" stroke-width="3"><path d="M5 12l5 5 9-10"/></svg></span>Flexible in-person and virtual sessions</div>
      <div class="why-item"><span class="tick"><svg width="16" height="16" viewBox="0 0 24 24" fill="none" stroke="#5ab3c3" stroke-width="3"><path d="M5 12l5 5 9-10"/></svg></span>Strong ties to the DC community</div>
    </div>
    <span class="btn">DISCOVER MORE</span>
  </div>
  <div class="why-photo photo" role="img" aria-label="Smiling woman seated in a calm counselling room"></div>
</section>

<section class="services">
  <div class="services-head">
    <h2 class="section-title">Novo Health <span class="mark">Services</span></h2>
    <p>We offer a wide range of mental health services tailored to your needs.</p>
  </div>
  <div class="service-grid">
    <div class="service">
      <div class="service-photo photo" role="img" aria-label="One-on-one therapy conversation" style="background:linear-gradient(135deg,#c9b49e,#8d7360)"></div>
      <h4>Individual Therapy</h4>
      <p>Personalized support for emotional well-being.</p>
    </div>
    <div class="service is-highlight">
      <div class="service-photo photo" role="img" aria-label="Counsellor supporting a person in crisis" style="background:linear-gradient(135deg,#e7ddd3,#b8a798)"></div>
      <h4>Crisis Intervention</h4>
      <p>Immediate support during difficult times.</p>
    </div>
    <div class="service">
      <div class="service-photo photo" role="img" aria-label="Client joining a video therapy session at home" style="background:linear-gradient(135deg,#dfe6e2,#9fb2a8)"></div>
      <h4>Telehealth Services</h4>
      <p>Accessible care from the comfort of your home.</p>
    </div>
    <div class="service">
      <div class="service-photo photo" role="img" aria-label="Community support group meeting" style="background:linear-gradient(135deg,#e9e4dc,#b9aa96)"></div>
      <h4>Community Support</h4>
      <p>Bringing health services to your environment.</p>
    </div>
  </div>
  <div class="explore">EXPLORE ALL SERVICES</div>
</section>

<section class="testimonials">
  <div class="quote-mark" aria-hidden="true">&ldquo;</div>
  <h2 class="section-title">Client <span class="mark">Testimonials</span></h2>
  <blockquote>The team listened to me from the very first visit and helped me build steady habits for hard days. Sessions felt warm and never rushed, and I always left with a clear next step. Scheduling was simple, the staff were kind, and for the first time in years I feel hopeful about the road ahead.</blockquote>
  <div class="client-name">Mara Ellis</div>
  <div class="client-role">A satisfied client</div>
  <span class="arrow" style="left:110px"><svg width="14" height="14" viewBox="0 0 24 24" fill="none" stroke="#0f2a47" stroke-width="2.5"><path d="M15 5l-7 7 7 7"/></svg></span>
  <span class="arrow" style="right:110px"><svg width="14" height="14" viewBox="0 0 24 24" fill="none" stroke="#f47b20" stroke-width="2.5"><path d="M9 5l7 7-7 7"/></svg></span>
</section>

<div class="cta">
  <h2>Ready to take the first step?</h2>
  <span class="cta-btn">REQUEST AN APPOINTMENT</span>
  <span class="cta-phone"><svg width="20" height="20" viewBox="0 0 24 24" fill="#0f2a47"><path d="M6.6 10.8a15.1 15.1 0 0 0 6.6 6.6l2.2-2.2c.3-.3.7-.4 1-.2 1.1.4 2.3.6 3.6.6.6 0 1 .4 1 1V20c0 .6-.4 1-1 1A17 17 0 0 1 3 4c0-.6.4-1 1-1h3.5c.6 0 1 .4 1 1 0 1.3.2 2.5.6 3.6.1.3 0 .7-.2 1z"/></svg></span>
</div>

<footer class="site-footer">
  <div class="footer-brand"><span class="brand-dot"></span>Novo Health Services</div>
  <div class="footer-col" style="left:440px">
    <h5>Quick Links</h5>
    <ul><li>Home</li><li>About Us</li><li>Services</li><li>Resources</li><li>Careers</li><li>Contact Us</li></ul>
  </div>
  <div class="footer-col" style="left:620px;width:240px">
    <h5>Contact Info</h5>
    <div class="contact-item"><svg width="16" height="16" viewBox="0 0 24 24" fill="#f47b20"><path d="M6.6 10.8a15.1 15.1 0 0 0 6.6 6.6l2.2-2.2c.3-.3.7-.4 1-.2 1.1.4 2.3.6 3.6.6.6 0 1 .4 1 1V20c0 .6-.4 1-1 1A17 17 0 0 1 3 4c0-.6.4-1 1-1h3.5c.6 0 1 .4 1 1 0 1.3.2 2.5.6 3.6.1.3 0 .7-.2 1z"/></svg><div><b>Phone</b>(202) 555-0148</div></div>
    <div class="contact-item"><svg width="16" height="16" viewBox="0 0 24 24" fill="none" stroke="#f47b20" stroke-width="2"><rect x="3" y="5" width="18" height="14" rx="2"/><path d="M3 7l9 6 9-6"/></svg><div><b>Email</b>info@novohealthservices.com</div></div>
    <div class="contact-item"><svg width="16" height="16" viewBox="0 0 24 24" fill="#f47b20"><path d="M12 2a7 7 0 0 0-7 7c0 5 7 13 7 13s7-8 7-13a7 7 0 0 0-7-7zm0 9.5A2.5 2.5 0 1 1 12 6.5a2.5 2.5 0 0 1 0 5z"/></svg><div><b>Location</b>480 Harbor Lane,<br>Washington, DC 20002</div></div>
  </div>
  <div class="footer-col newsletter" style="left:880px;width:240px">
    <h5>Newsletter</h5>
    <p>Subscribe Our Newsletter for latest news</p>
    <div class="subscribe"><span>Enter your email</span><i><svg width="14" height="14" viewBox="0 0 24 24" fill="none" stroke="#fff" stroke-width="2.5"><path d="M5 12h14M13 6l6 6-6 6"/></svg></i></div>
  </div>
  <div class="copyright">© Copyright 2025 Novo Health Services | All rights reserved</div>
</footer>

</body>
</html>
```